Fire Risk Assessment App needs a sleek UI design

I need a sleek, modern but professional design for my 5 page Fire Risk Assessment App. Include gradient background, fire themed colours including reds, yellows, light orange and a touch of black. Design must ooze simplicity and professionalism. This is for the UK market. See attached images and word doc for more information.

Target Market(s)

General public and business owners

Industry/Entity Type

Technology / Fire Safety

Colors
00AB8E
00BBA5
67D7C9
C6EFE9
E9F9F6
59FF00
82FF00
B8FF75
E3FFCB
F4FFEA
FFC000
F8CF3A
FAE287
FDF2CF
FEFAEE
F0912C
F2A743
F7CA91
FBE8D2
FDF5EE
EE7325
F08F49
F5BC92
FAE3D3
FDF4ED
EB3D1F
EC4F4E
F09395
F8D3D4
FCEDEE

```html
<!DOCTYPE html>
<html lang="en">
<head>
<meta charset="utf-8">
<title>Fire Risk Assessment App – UI Screens</title>
<link href="https://fonts.googleapis.com/css2?family=Montserrat:wght@400;500;600&display=swap" rel="stylesheet">
<style>
:root{
  --canvas:#e4e4e4;
  --orange:#fe9029;
  --orange-text:#f5892a;
  --red:#eb3d4e;
  --black:#111111;
  --ink:#1e1e1e;
  --white:#ffffff;
  --screen-top:#fdf4ec;
  --screen-bottom:#f9efe8;
  --paper:#dcdcdc;
}
*{box-sizing:border-box;margin:0;padding:0}
html,body{width:1200px;height:820px;overflow:hidden;background:var(--canvas);font-family:'Montserrat',sans-serif;color:var(--ink)}
.stage{position:absolute;left:0;top:0;width:1464px;height:1000px;transform:scale(.8197);transform-origin:0 0}
.screen{position:absolute;top:52px;width:414px;height:896px;overflow:hidden;background:linear-gradient(180deg,var(--screen-top) 0%,#faf3ee 60%,var(--screen-bottom) 100%)}
.screen--welcome{left:54px}
.screen--dashboard{left:517px}
.screen--support{left:990px}
.abs{position:absolute}
.flames{position:absolute;left:0;bottom:0;width:100%;height:150px;background:linear-gradient(180deg,rgba(250,220,190,0) 0%,rgba(240,170,110,.35) 60%,rgba(235,150,90,.45) 100%)}
.headline{position:absolute;left:0;width:100%;text-align:center;color:var(--orange-text);font-size:17px;line-height:34px;letter-spacing:.2px}
.caption{position:absolute;left:0;width:100%;text-align:center;font-size:16.5px;line-height:34px}
.pill{position:absolute;left:72px;width:270px;height:48px;border-radius:24px;background:var(--orange);color:var(--white);font-size:15px;display:flex;align-items:center;padding-left:16px;letter-spacing:.2px}
.pill .icon{position:absolute;right:12px;top:6px;width:36px;height:36px}
.paper{position:absolute;background:var(--paper)}
.qa-card{position:absolute;left:162px;top:155px;width:185px;height:212px;background:var(--white);padding:10px 12px;font-size:7.5px;line-height:18px}
.qa-card .gap{height:8px}
.qa-tools{position:absolute;left:12px;top:178px;display:flex;gap:13px}
.fingerprint{position:absolute;left:309px;top:140px;width:65px;height:65px;border-radius:50%;background:radial-gradient(circle,#444 0%,#888 45%,#fff 70%);box-shadow:0 2px 8px rgba(0,0,0,.12)}
.field{position:absolute;left:36px;top:480px;width:342px;height:36px;border-bottom:1.5px solid #333;color:#999;font-size:16px;padding-top:2px}
.field svg{position:absolute;right:2px;top:0}
.header-title{position:absolute;top:34px;color:var(--orange-text);font-size:17px}
.label{position:absolute;font-size:13.5px;font-weight:500;text-align:center}
.row{position:absolute;display:flex;align-items:center;gap:14px;font-size:15px}
.radio{width:16px;height:16px;border-radius:50%;border:2px solid var(--ink);display:flex;align-items:center;justify-content:center}
.radio::after{content:"";width:8px;height:8px;border-radius:50%;background:var(--ink)}
.navbar{position:absolute;left:0;bottom:0;width:100%;height:66px;background:var(--orange);display:flex}
.navbar .tab{flex:1;display:flex;align-items:center;justify-content:center}
.navbar .tab--active{background:var(--black)}
.response-box{position:absolute;left:13px;top:94px;width:388px;height:393px;background:var(--white);border-radius:10px}
.response-box .hint{position:absolute;left:25px;top:34px;font-size:8.5px;color:#444}
.response-box svg{position:absolute;right:26px;top:28px}
.send{position:absolute;left:311px;top:509px;width:90px;height:48px;border-radius:24px;background:var(--orange);color:var(--white);font-size:15px;display:flex;align-items:center;justify-content:center}
</style>
</head>
<body>
<div class="stage">

<!-- Welcome screen -->
<section class="screen screen--welcome">
  <div class="flames" role="img" aria-label="Soft flame artwork along the bottom edge"></div>
  <div class="headline" style="top:49px">THE MOST "USER FRIENDLY" FIRE RISK<br>ASSESSMENT APP AVAILABLE</div>
  <div class="paper" style="left:95px;top:215px;width:190px;height:200px;transform:rotate(-28deg);background:#e2e0df"></div>
  <div class="paper" style="left:110px;top:210px;width:190px;height:200px;transform:rotate(-14deg);background:#ebe9e8"></div>
  <div class="qa-card">
    <div>FIRE RISK ASSESSMENT</div>
    <div>FIRE HAZARDS</div>
    <div>SECTION 7.00/30.00</div>
    <div>ELECTRONIC SOURCES OF IGNITION</div>
    <div class="gap"></div>
    <div>Q:7.01</div>
    <div>ARC REASONABLE MEASURES</div>
    <div>TAKEN TO PREVENT FIRES OF</div>
    <div>ELECTRICAL ORIGIN?</div>
    <div class="qa-tools">
      <svg width="18" height="18" viewBox="0 0 18 18"><circle cx="9" cy="9" r="9" fill="#000"/><path d="M5 9.5l2.7 2.7L13 6.5" stroke="#fff" stroke-width="2" fill="none"/></svg>
      <svg width="18" height="18" viewBox="0 0 18 18"><circle cx="9" cy="9" r="9" fill="#000"/><path d="M6 6l6 6M12 6l-6 6" stroke="#fff" stroke-width="2"/></svg>
      <svg width="18" height="18" viewBox="0 0 18 18"><circle cx="9" cy="9" r="9" fill="#000"/><rect x="4.5" y="7.8" width="9" height="2.4" fill="#fff"/></svg>
      <svg width="24" height="18" viewBox="0 0 24 18"><path d="M6 15a4.5 4.5 0 0 1 0-9 6 6 0 0 1 11.5 1.5A3.8 3.8 0 0 1 18 15" stroke="#000" stroke-width="1.4" fill="none"/><path d="M12 17V9M9 11.5l3-3 3 3" stroke="#000" stroke-width="1.4" fill="none"/></svg>
      <svg width="14" height="20" viewBox="0 0 14 20"><rect x="4" y="1" width="6" height="11" rx="3" fill="#000"/><path d="M1.5 9a5.5 5.5 0 0 0 11 0M7 14.5V19M4 19h6" stroke="#000" stroke-width="1.4" fill="none"/></svg>
    </div>
  </div>
  <div class="fingerprint" role="img" aria-label="Fingerprint sign-in icon"></div>
  <div class="field">TYPE HERE
    <svg width="14" height="22" viewBox="0 0 14 22"><rect x="4" y="1" width="6" height="12" rx="3" fill="#000"/><path d="M1.5 10a5.5 5.5 0 0 0 11 0M7 15.5V21M4 21h6" stroke="#000" stroke-width="1.4" fill="none"/></svg>
  </div>
  <div class="pill" style="top:564px">CREATE A FREE ACCOUNT
    <svg class="icon" viewBox="0 0 36 36"><circle cx="18" cy="18" r="13" stroke="#fff" stroke-width="1.6" fill="none"/><circle cx="18" cy="15" r="4.5" stroke="#fff" stroke-width="1.6" fill="none"/><path d="M10 27c2-4 5-5.5 8-5.5s6 1.5 8 5.5" stroke="#fff" stroke-width="1.6" fill="none"/></svg>
  </div>
  <div class="caption" style="top:645px">ANY RESPONSIBLE PERSON CAN DO IT</div>
  <div class="pill" style="top:707px">CUSTOMER LOG IN
    <svg class="icon" viewBox="0 0 36 36"><circle cx="17" cy="12" r="5" stroke="#fff" stroke-width="1.6" fill="none"/><path d="M8 27c1-5 5-8 9-8 2 0 3 .4 4 1" stroke="#fff" stroke-width="1.6" fill="none"/><path d="M25 21v8M21 25h8" stroke="#fff" stroke-width="1.6"/></svg>
  </div>
  <div class="caption" style="top:788px">CREATED AND ENDORSED BY BRITISH<br>FIREFIGHTERS.</div>
</section>

<!-- Dashboard screen -->
<section class="screen screen--dashboard">
  <div class="flames" role="img" aria-label="Soft flame artwork above the navigation bar" style="bottom:66px;height:90px"></div>
  <svg class="abs" style="left:32px;top:34px" width="32" height="26" viewBox="0 0 32 26"><path d="M3 22a13 13 0 1 1 26 0z" fill="var(--orange)"/><path d="M8 20a8 8 0 0 1 16 0" stroke="#fff" stroke-width="2" fill="none"/><path d="M16 20l5-7" stroke="#fff" stroke-width="2.4"/></svg>
  <div class="header-title" style="left:0;width:414px;text-align:center;padding-left:2px">DASHBOARD</div>
  <svg class="abs" style="left:0;top:0" width="414" height="260" viewBox="0 0 414 260">
    <path d="M100 180L190 132M224 132L312 185" stroke="#222" stroke-width="1" stroke-dasharray="4 3"/>
    <circle cx="207" cy="118" r="21" fill="#fff"/>
    <circle cx="207" cy="118" r="13" fill="var(--red)"/>
    <path d="M207 111v14M200 118h14" stroke="#fff" stroke-width="3"/>
    <circle cx="85" cy="196" r="22" fill="var(--orange)"/>
    <path d="M75 197l10-9 10 9M78 195v9h14v-9" stroke="#fff" stroke-width="1.8" fill="#dfe9f7"/>
    <rect x="82" y="196" width="6" height="5" fill="#6b8fd1"/>
    <circle cx="330" cy="196" r="22" fill="#fff" stroke="#ddd"/>
    <path d="M319 197l11-10 11 10M322 195v10h16v-10" stroke="#222" stroke-width="1.5" fill="none"/>
    <rect x="327" y="198" width="6" height="7" fill="none" stroke="#222"/>
  </svg>
  <div class="label" style="left:142px;top:161px;width:120px;line-height:24px">FIRE RISK<br>ASSESSMENT</div>
  <div class="label" style="left:25px;top:239px;width:120px">COMMERCIAL</div>
  <div class="label" style="left:269px;top:239px;width:120px">RESIDENTIAL</div>

  <div class="pill" style="top:306px">COMPLETE
    <svg class="icon" viewBox="0 0 36 36"><circle cx="18" cy="18" r="18" fill="#fff"/><circle cx="18" cy="18" r="14" fill="#1fa336"/><path d="M11 18.5l5 5 9-10" stroke="#fff" stroke-width="3" fill="none"/></svg>
  </div>
  <div class="row" style="left:92px;top:382px">
    <svg width="26" height="22" viewBox="0 0 26 22"><path d="M2 11L13 2l11 9" stroke="var(--orange)" stroke-width="2.4" fill="none"/><path d="M5 10v11h16V10L13 4z" fill="#dfe9f7"/><rect x="10" y="12" width="6" height="5" fill="#6b8fd1"/></svg>
    <span>ELM LANE BARBERS</span>
  </div>

  <div class="pill" style="top:445px">IN PROGRESS
    <svg class="icon" viewBox="0 0 36 36"><circle cx="18" cy="18" r="18" fill="#fff"/><circle cx="18" cy="18" r="13" stroke="#111" stroke-width="1.6" stroke-dasharray="6 2" fill="none"/><path d="M12 18.5l4.5 4.5 8-9" stroke="#111" stroke-width="2" fill="none"/></svg>
  </div>
  <div class="row" style="left:84px;top:522px"><span class="radio"></span><span>NORTHFIELD RD SCHOOL</span></div>
  <div class="row" style="left:84px;top:556px"><span class="radio"></span><span>WILLOW COURT CARE HOME</span></div>

  <div class="pill" style="top:620px">PURCHASES
    <svg class="icon" viewBox="0 0 36 36"><circle cx="18" cy="18" r="18" fill="#fff"/><path d="M9 11h3l3 11h11l2-8H13" stroke="#111" stroke-width="2" fill="none"/><circle cx="16" cy="26" r="1.8" fill="#111"/><circle cx="25" cy="26" r="1.8" fill="#111"/></svg>
  </div>
  <div class="row" style="left:41px;top:697px"><span class="radio"></span><span>RESIDENTIAL FIRE RISK ASSESSMENT</span></div>
  <div class="row" style="left:41px;top:731px"><span class="radio"></span><span>COMMERCIAL FIRE RISK ASSESSMENT</span></div>
  <div class="row" style="left:41px;top:765px"><span class="radio"></span><span>COMMERCIAL FIRE RISK ASSESSMENT</span></div>

  <nav class="navbar">
    <div class="tab tab--active" style="flex:0 0 88px"><svg width="32" height="26" viewBox="0 0 32 26"><path d="M4 21a12 12 0 1 1 24 0" stroke="#fff" stroke-width="2.2" fill="none"/><path d="M9 21a7 7 0 0 1 14 0" stroke="#fff" stroke-width="2" fill="none"/><path d="M16 21l5-7" stroke="#fff" stroke-width="2.4"/></svg></div>
    <div class="tab"><svg width="30" height="22" viewBox="0 0 30 22"><rect x="5" y="2" width="23" height="15" rx="2" stroke="#fff" stroke-width="1.6" fill="none"/><rect x="2" y="5" width="23" height="15" rx="2" stroke="#fff" stroke-width="1.6" fill="var(--orange)"/><path d="M2 10h23M6 15h6" stroke="#fff" stroke-width="1.6"/></svg></div>
    <div class="tab"><svg width="28" height="26" viewBox="0 0 28 26"><path d="M2 2h24v16H10l-6 6v-6H2z" fill="#fff"/><path d="M7 8h14M7 12h10" stroke="var(--orange)" stroke-width="2"/></svg></div>
    <div class="tab"><svg width="32" height="28" viewBox="0 0 32 28"><circle cx="22" cy="5" r="3" fill="#fff"/><path d="M12 26l5-7-3-5 6-4 4 5h5M17 19l3 7M14 14l-5 2" stroke="#fff" stroke-width="2.4" fill="none"/><path d="M3 22c3-1 4-5 3-8 2 2 4 5 2 9z" fill="#fff"/></svg></div>
  </nav>
</section>

<!-- Technical support screen -->
<section class="screen screen--support">
  <div class="flames" role="img" aria-label="Soft flame artwork above the navigation bar" style="bottom:66px;height:90px"></div>
  <svg class="abs" style="left:35px;top:34px" width="26" height="24" viewBox="0 0 26 24"><path d="M2 2h22v14H9l-6 6v-6H2z" fill="var(--orange)"/><path d="M6 7h14M6 11h9" stroke="#fff" stroke-width="2"/></svg>
  <div class="header-title" style="left:0;width:434px;text-align:center">TECHNICAL SUPPORT</div>
  <div class="response-box">
    <div class="hint">TYPE / RECORD YOUR RESPONSE HERE....</div>
    <svg width="12" height="20" viewBox="0 0 14 22"><rect x="4" y="1" width="6" height="12" rx="3" fill="#000"/><path d="M1.5 10a5.5 5.5 0 0 0 11 0M7 15.5V21M4 21h6" stroke="#000" stroke-width="1.4" fill="none"/></svg>
  </div>
  <div class="send">SEND</div>
  <nav class="navbar">
    <div class="tab"><svg width="32" height="26" viewBox="0 0 32 26"><path d="M4 21a12 12 0 1 1 24 0" stroke="#fff" stroke-width="2.2" fill="none"/><path d="M9 21a7 7 0 0 1 14 0" stroke="#fff" stroke-width="2" fill="none"/><path d="M16 21l5-7" stroke="#fff" stroke-width="2.4"/></svg></div>
    <div class="tab"><svg width="30" height="22" viewBox="0 0 30 22"><rect x="5" y="2" width="23" height="15" rx="2" stroke="#fff" stroke-width="1.6" fill="none"/><rect x="2" y="5" width="23" height="15" rx="2" stroke="#fff" stroke-width="1.6" fill="var(--orange)"/><path d="M2 10h23M6 15h6" stroke="#fff" stroke-width="1.6"/></svg></div>
    <div class="tab tab--active" style="flex:0 0 80px"><svg width="28" height="26" viewBox="0 0 28 26"><path d="M2 2h24v16H10l-6 6v-6H2z" fill="#fff"/><path d="M7 8h14M7 12h10" stroke="#111" stroke-width="2"/></svg></div>
    <div class="tab" style="flex:0 0 114px"><svg width="32" height="28" viewBox="0 0 32 28"><circle cx="22" cy="5" r="3" fill="#fff"/><path d="M12 26l5-7-3-5 6-4 4 5h5M17 19l3 7M14 14l-5 2" stroke="#fff" stroke-width="2.4" fill="none"/><path d="M3 22c3-1 4-5 3-8 2 2 4 5 2 9z" fill="#fff"/></svg></div>
  </nav>
</section>

</div>
</body>
</html>
```